Podiatry (services) Business Card

I need a business design for a New Podiatry Service.
the Podiatry services will include all aspects of podiatry including;
general podiatry for all ages
corns and callus treatment
Ingrown toenails & nail surgery
Forefoot, arch and heel pain
Gait analysis
Sports Podiatry and Orthotics
Paediatric Assessments
Diabetes Foot Assessment

I would like the back of the card to have space for next appointment day and time.

I would like a nice design that is simple yet catchy. I don't like cluttered business cards. I like things to be simple yet stand out because of the finer details.

I like the colours blue and white but I'm open to other designs that have different colours.

Business

Bluewren Podiatry (Business name)

Marisol Tenbury - Podiatrist
M.Pod.P., B.Hlth. Sci, MFLsoc

Address: 58 Coleby St, Marrowdale North Vic, 3164
Phone: (03) 9416 2738
Fax: (03) 9523 4178

```html
<!DOCTYPE html>
<html lang="en">
<head>
<meta charset="utf-8">
<title>Bluewren Podiatry – Business Card</title>
<link rel="stylesheet" href="https://fonts.googleapis.com/css2?family=Open+Sans:wght@400;600;700&display=swap">
<style>
  :root {
    --brand-blue: #1a7cc4;
    --ink: #2b2b2b;
    --card: #ffffff;
    --stage: #eef1f4;
    --rule: #3a3a3a;
  }
  * { box-sizing: border-box; margin: 0; padding: 0; }
  html, body {
    width: 1200px; height: 900px; overflow: hidden;
    background: var(--stage);
    font-family: "Open Sans", Arial, sans-serif;
    color: var(--ink);
  }
  .canvas { position: relative; width: 1200px; height: 900px; }

  .card {
    position: absolute;
    width: 540px; height: 330px;
    background: var(--card);
    box-shadow: 0 10px 30px rgba(0,0,0,0.12);
  }
  .card--back  { left: 40px;  top: 100px; }
  .card--front { left: 620px; top: 470px; }

  /* Back: appointment + services */
  .appointment { position: absolute; left: 40px; top: 52px; width: 240px; }
  .appointment__title {
    color: var(--brand-blue); font-weight: 700; font-size: 19px; letter-spacing: 0.3px;
  }
  .appointment__field {
    display: flex; align-items: baseline; margin-top: 14px;
    color: var(--brand-blue); font-weight: 700; font-size: 14px;
  }
  .appointment__field--name { margin-left: 8px; }
  .appointment__field--when { margin-left: 16px; }
  .appointment__line {
    flex: 1; border-bottom: 2px dotted var(--rule); margin: 0 6px; height: 1px;
  }
  .appointment__line--short { flex: 0 0 82px; }

  .services { position: absolute; left: 296px; top: 72px; }
  .services__title {
    color: var(--brand-blue); font-weight: 700; font-size: 17px; margin-bottom: 6px;
  }
  .services__list { list-style: none; }
  .services__item {
    position: relative; padding-left: 16px;
    font-weight: 700; font-size: 12.5px; line-height: 20px; color: var(--ink);
  }
  .services__item::before {
    content: ""; position: absolute; left: 2px; top: 7px;
    width: 6px; height: 6px; border-radius: 50%; background: var(--brand-blue);
  }

  /* Front: wordmark + contact */
  .wordmark {
    position: absolute; left: 40px; top: 64px;
    display: flex; align-items: center; gap: 10px;
  }
  .wordmark__dot { width: 18px; height: 18px; border-radius: 50%; background: var(--brand-blue); }
  .wordmark__name {
    color: var(--brand-blue); font-weight: 400; font-size: 20px;
    letter-spacing: 1.5px; text-transform: uppercase; white-space: nowrap;
  }

  .contact { position: absolute; left: 300px; top: 118px; width: 220px; font-size: 13px; }
  .contact__name { font-size: 15px; font-weight: 700; color: var(--brand-blue); white-space: nowrap; }
  .contact__role { font-size: 12px; font-weight: 400; color: var(--ink); }
  .contact__creds { margin-top: 2px; margin-left: 12px; font-size: 11.5px; white-space: nowrap; }
  .contact__address { margin-top: 18px; margin-left: 26px; line-height: 20px; }
  .contact__lines { margin-top: 22px; margin-left: 40px; line-height: 21px; }
  .contact__line { display: flex; align-items: center; gap: 6px; }
  .contact__icon { width: 12px; height: 12px; fill: var(--brand-blue); }
</style>
</head>
<body>
<main class="canvas">

  <section class="card card--back" aria-label="Card back: appointment and services">
    <div class="appointment">
      <h2 class="appointment__title">APPOINTMENT</h2>
      <div class="appointment__field appointment__field--name">Name:<span class="appointment__line"></span></div>
      <div class="appointment__field appointment__field--when">Date:<span class="appointment__line appointment__line--short"></span>Time:<span class="appointment__line"></span></div>
    </div>
    <div class="services">
      <h3 class="services__title">Services</h3>
      <ul class="services__list">
        <li class="services__item">General podiatry for all ages</li>
        <li class="services__item">Corns and callus treatment</li>
        <li class="services__item">Ingrown toenails &amp; nail surgery</li>
        <li class="services__item">Forefoot, arch and heel pain</li>
        <li class="services__item">Gait analysis</li>
        <li class="services__item">Sports Podiatry and Orthotics</li>
        <li class="services__item">Paediatric Assessments</li>
        <li class="services__item">Diabetes Foot Assessment</li>
      </ul>
    </div>
  </section>

  <section class="card card--front" aria-label="Card front: practice and contact details">
    <div class="wordmark">
      <span class="wordmark__dot"></span>
      <span class="wordmark__name">Bluewren Podiatry</span>
    </div>
    <div class="contact">
      <p class="contact__name">Marisol Tenbury <span class="contact__role">- Podiatrist</span></p>
      <p class="contact__creds">M.Pod.P., B.Hlth. Sci, MFLsoc</p>
      <p class="contact__address">58 Coleby St, Marrowdale<br>North Vic, 3164</p>
      <div class="contact__lines">
        <p class="contact__line">
          <svg class="contact__icon" viewBox="0 0 24 24" aria-hidden="true"><path d="M6.6 10.8a15.1 15.1 0 0 0 6.6 6.6l2.2-2.2c.3-.3.7-.4 1-.2 1.1.4 2.3.6 3.6.6.6 0 1 .4 1 1V20c0 .6-.4 1-1 1A17 17 0 0 1 3 4c0-.6.4-1 1-1h3.5c.6 0 1 .4 1 1 0 1.3.2 2.5.6 3.6.1.3 0 .7-.2 1z"/></svg>
          (03) 9416 2738
        </p>
        <p class="contact__line">
          <svg class="contact__icon" viewBox="0 0 24 24" aria-hidden="true"><path d="M7 2h8l3 3v4H7z M3 10h18v10H3z M6 13h4v2H6z M13 13h2v2h-2z M16 13h2v2h-2z M13 16h2v2h-2z M16 16h2v2h-2z"/></svg>
          (03) 9523 4178
        </p>
      </div>
    </div>
  </section>

</main>
</body>
</html>
```